Logo & nopcommerce theme design for a webshop in gadgets & lifestyle products

We are looking for someone who can design a logo and a nopcommerce theme for our webshop. The name of the shop is Lumavorp. The logo should also be used for plaztrove. In the attached file we have an example of a theme that is close what we are looking for. The coloring should be different but the lay-out is ok. Only on the left we want a column to choose a sub category and a column where you can set some filters to search in detail for a product.

Industry/Entity Type

Shop

Number of Pages Required

1 page

Requirements
Must have
• The Nopcommerce theme for 3.40 should have a professional look, not to color full and for the rest we leave it to the designer
Nice to have
• n/a
Should not have
• n/a

```html
<!DOCTYPE html>
<html lang="en">
<head>
<meta charset="utf-8">
<title>Lumavorp – Gadgets &amp; Lifestyle</title>
<link rel="stylesheet" href="https://fonts.googleapis.com/css2?family=Open+Sans:wght@300;400;600;700&display=swap">
<style>
:root{
  --accent:#d6503e;
  --ink:#333333;
  --muted:#8a8a8a;
  --line:#dddddd;
  --page:#eeeeee;
  --card:#ffffff;
  --dark:#3b3c3e;
  --img:#e4e4e4;
  --blue:#2f9bd8;
  --tone-black:radial-gradient(ellipse 48% 40% at 50% 52%,#161616 0%,#3a3a3a 45%,#bdbdbd 80%,#e6e6e6 100%);
  --tone-silver:radial-gradient(ellipse 48% 42% at 50% 52%,#8e9094 0%,#c4c6c9 50%,#e2e2e2 85%,#e8e8e8 100%);
  --tone-white:radial-gradient(ellipse 40% 44% at 50% 52%,#fafafa 0%,#d4d6d8 55%,#e6e6e6 100%);
  --tone-wood:radial-gradient(ellipse 50% 44% at 50% 52%,#2a1f18 0%,#8c6a4a 50%,#d9d4cf 85%,#e6e6e6 100%);
}
*{box-sizing:border-box;margin:0;padding:0}
html,body{width:1200px;height:3267px;overflow:hidden}
body{position:relative;background:var(--page);font-family:"Open Sans",Arial,sans-serif;color:var(--ink);font-size:12px}
ul{list-style:none}
.abs{position:absolute}

/* top */
.topline{left:0;top:0;width:1200px;height:6px;background:var(--dark)}
.topbar{left:183px;top:13px;font-size:10px;color:#555;display:flex;align-items:center;gap:6px}
.topbar b{color:var(--ink)}
.logo{left:183px;top:80px;display:flex;align-items:flex-end;gap:8px}
.logo-name{font-size:50px;font-weight:700;letter-spacing:-1px;color:var(--ink);line-height:1}
.logo-dot{width:14px;height:14px;background:var(--accent);margin-bottom:9px}
.lang{left:877px;top:6px;display:flex;z-index:6}
.lang span{width:28px;height:38px;display:flex;align-items:center;justify-content:center;font-size:10px;color:#fff;background:#6a6a6a}
.lang span.on{background:var(--dark)}
.lang span.bag{background:#2a2a2a}
.lang span.nav{width:17px;background:#dcdcdc;color:#555}
.search{left:982px;top:78px;width:37px;height:37px;background:#fff;border:1px solid var(--line);display:flex;align-items:center;justify-content:center}

.navbar{left:0;top:155px;width:1200px;height:32px;background:var(--dark)}
.menu{position:absolute;left:183px;top:0;display:flex;height:32px}
.menu li{padding:0 14px;line-height:32px;color:#fff;font-size:12px}
.menu li.active{background:var(--accent)}

/* cart */
.cart{left:747px;top:6px;width:235px;background:#fff;box-shadow:0 2px 6px rgba(0,0,0,.2);z-index:5}
.cart h4{font-size:10px;font-weight:400;height:38px;line-height:38px;padding:0 14px;border-bottom:1px solid var(--line)}
.cart li{display:flex;align-items:center;padding:6px 14px;border-bottom:1px solid #eee;gap:8px}
.cart .x{color:var(--accent);font-size:10px}
.cart .it{flex:1;font-size:9px;line-height:1.5}
.cart .it b{font-weight:600;display:block}
.cart .th{width:26px;height:26px;background:var(--tone-black)}
.cart .total{display:flex;justify-content:space-between;padding:12px 14px;font-size:9px;font-weight:700}
.cart .btns{display:flex}
.cart .btns span{flex:1;height:38px;display:flex;align-items:center;justify-content:center;color:#fff;font-size:10px;font-weight:700;background:var(--dark)}
.cart .btns span+span{background:var(--accent)}

/* hero */
.hero{left:183px;top:224px;width:836px;height:266px;background:linear-gradient(90deg,#0c0c0c 0%,#1d1d1d 100%);box-shadow:0 8px 10px -6px rgba(0,0,0,.4)}
.hero .shot{position:absolute;left:330px;top:0;width:506px;height:266px;background:radial-gradient(ellipse 60% 55% at 55% 45%,#5b5b5d 0%,#2b2b2d 45%,#0f0f0f 80%),#111}
.hero .copy{position:absolute;left:80px;top:31px;color:#fff;line-height:1.05}
.hero .l1{font-size:31px;font-weight:300}
.hero .l2{font-size:40px;font-weight:400}
.hero .l3{font-size:31px;font-weight:400}
.hero .l4{font-size:56px;font-weight:700;color:var(--blue)}
.hero .l4 small{font-size:16px;font-weight:600;color:var(--blue);margin-left:10px;vertical-align:middle}
.hero .l5{font-size:31px;font-weight:300}
.arrow{width:26px;height:26px;background:#fff;display:flex;align-items:center;justify-content:center}
.dots{left:575px;top:464px;display:flex;gap:5px}
.dots i{width:8px;height:8px;border-radius:50%;background:#fff}
.dots i:first-child{background:var(--accent)}

/* featured */
.featured{left:183px;top:516px;width:836px;height:279px;background:#4a4b4d}
.fcard{position:absolute;top:22px;width:176px;height:235px;background:#fff;overflow:hidden;text-align:center}
.fcard .pic{position:absolute;left:10px;top:14px;width:156px;height:116px}
.ribbon{position:absolute;left:-28px;top:12px;width:100px;transform:rotate(-45deg);background:var(--accent);color:#fff;font-size:8px;font-weight:700;padding:3px 0}
.fcard .nm{position:absolute;top:140px;width:100%;font-size:10px;color:#555}
.fcard .pr{position:absolute;top:152px;width:100%;font-size:17px}
.fcard .old{position:absolute;top:178px;width:100%;font-size:10px}
.fcard .old s{color:var(--muted)}
.fcard .old em{font-style:normal;color:var(--accent)}
.fcard .btn{position:absolute;left:38px;top:199px;width:100px;height:22px;background:var(--dark);color:#fff;font-size:10px;font-weight:700;line-height:22px}

/* tones */
.t-black{background:var(--tone-black)}
.t-silver{background:var(--tone-silver)}
.t-white{background:var(--tone-white)}
.t-wood{background:var(--tone-wood)}
.t-thermo{background:radial-gradient(circle at 50% 50%,#e46a3a 0%,#2a2a2a 22%,#b5693a 34%,#7a3f1f 100%)}
.t-tv{background:radial-gradient(ellipse 50% 40% at 50% 48%,#f7d43a 0%,#e8742a 40%,#b8231a 75%,#e6e6e6 100%)}

/* sidebar */
.box{background:#fff;border:1px solid var(--line)}
.cats{left:183px;top:838px;width:172px;height:430px}
.box h3{font-size:15px;font-weight:400;padding:6px 12px;border-bottom:1px solid var(--line);background:#f5f5f5}
.cats li{height:30px;line-height:30px;padding-left:12px;font-size:10px;color:#555}
.cats li.on{background:var(--accent);color:#fff}
.filters{left:183px;top:1287px;width:172px;height:1039px;padding-bottom:10px}
.filters .grp+.grp h3{border-top:1px solid var(--line);margin-top:6px}
.filters li{height:30px;display:flex;align-items:center;gap:12px;padding-left:14px;font-size:10px;color:#555}
.filters li::before{content:"";width:10px;height:10px;border:1px solid #bbb;background:#fff}

/* products */
.sortbar{left:370px;top:838px;width:649px;height:33px;background:#fff;border:1px solid var(--line);display:flex;align-items:center;padding:0 12px;font-size:10px;color:#555;gap:8px}
.sortbar .sel{width:72px;height:20px;border:1px solid var(--line);display:flex;align-items:center;justify-content:space-between;padding:0 6px}
.sortbar u{color:var(--accent)}
.grid{left:370px;top:904px;width:649px;display:grid;grid-template-columns:repeat(3,192px);column-gap:36px;row-gap:32px}
.prod{position:relative;height:235px;background:#fff;border:1px solid var(--line)}
.prod .pic{position:absolute;left:6px;top:6px;width:178px;height:146px}
.prod .nm{position:absolute;left:12px;top:160px;font-size:10px;color:#555}
.prod .pr{position:absolute;left:12px;top:173px;font-size:16px}
.prod .foot{position:absolute;left:0;bottom:0;width:100%;height:36px;border-top:1px solid var(--line);display:flex;align-items:center;font-size:9px;color:#555}
.prod .foot span{flex:1;padding-left:12px}
.prod .foot s{color:var(--accent)}
.prod .foot .add{width:36px;height:36px;border-left:1px solid var(--line);display:flex;align-items:center;justify-content:center}

.pager{left:535px;top:2760px;display:flex;align-items:center;gap:10px;font-size:10px;color:#555}
.pager .pg{display:flex;background:#fff;border:1px solid var(--line)}
.pager .pg span{padding:5px 7px}
.pager .pg span.on{border-right:1px solid var(--line)}
.pager .pg.end span{padding:5px 9px}
.status{left:370px;top:2802px;width:649px;text-align:center;font-size:10px;font-style:italic;color:var(--muted)}

/* footer */
.footer{left:0;top:2953px;width:1200px;height:238px;background:var(--dark);color:#ddd}
.fcol{position:absolute;top:30px;width:186px}
.fcol h5{font-size:15px;font-weight:400;color:#fff;padding-bottom:10px;border-bottom:1px solid #5a5b5d;margin-bottom:14px}
.fcol li{font-size:10px;height:28px;display:flex;align-items:center;gap:10px}
.bottom{left:0;top:3191px;width:1200px;height:76px;background:#e6e6e6;font-size:10px;color:#555}
.bottom .copy{position:absolute;left:183px;top:32px}
.bottom .social{position:absolute;left:520px;top:29px;width:160px;display:flex;justify-content:center;gap:14px;font-size:11px;font-weight:600;color:var(--ink)}
</style>
</head>
<body>

<svg width="0" height="0" style="position:absolute">
  <symbol id="i-cart" viewBox="0 0 24 24"><path d="M1 3h4l3 11h11l3-8H7" fill="none" stroke="#d6503e" stroke-width="2"/><circle cx="9" cy="19" r="2" fill="#d6503e"/><circle cx="18" cy="19" r="2" fill="#d6503e"/></symbol>
  <symbol id="i-phone" viewBox="0 0 24 24"><path d="M6.6 10.8a15 15 0 0 0 6.6 6.6l2.2-2.2c.3-.3.7-.4 1-.2 1.1.4 2.3.6 3.6.6.6 0 1 .4 1 1V20c0 .6-.4 1-1 1A17 17 0 0 1 3 4c0-.6.4-1 1-1h3.5c.6 0 1 .4 1 1 0 1.3.2 2.5.6 3.6.1.3 0 .7-.2 1z"/></symbol>
  <symbol id="i-left" viewBox="0 0 8 10"><path d="M7 0L1 5l6 5z" fill="#222"/></symbol>
  <symbol id="i-right" viewBox="0 0 8 10"><path d="M1 0l6 5-6 5z" fill="#222"/></symbol>
</svg>

<div class="abs topline"></div>
<div class="abs topbar">
  <svg width="12" height="12" fill="#333"><use href="#i-phone"/></svg>
  <b>Call us:</b> (0000) 000.0000 • Signup • Sign in •
</div>

<div class="abs logo"><span class="logo-name">Lumavorp</span><span class="logo-dot"></span></div>

<div class="abs lang"><span class="on">EN</span><span>FR</span><span>GM</span><span class="bag">
  <svg width="11" height="11" viewBox="0 0 24 24"><path d="M4 8h16l-1 14H5z" fill="#fff"/><path d="M8 8a4 4 0 0 1 8 0" fill="none" stroke="#fff" stroke-width="2"/></svg></span><span class="nav">‹</span><span class="nav">›</span></div>

<div class="abs search"><svg width="16" height="16" viewBox="0 0 24 24"><circle cx="10" cy="10" r="7" fill="none" stroke="#333" stroke-width="2.5"/><path d="M15 15l7 7" stroke="#333" stroke-width="2.5"/></svg></div>

<div class="abs navbar">
  <ul class="menu"><li class="active">Home</li><li>Products</li><li>Register</li><li>Shop</li></ul>
</div>

<div class="abs cart">
  <h4>Shopping Cart</h4>
  <ul>
    <li><span class="x">✕</span><span class="it"><b>Fontry Double Bed, Oak</b>1 X - $215.00</span><span class="th" role="img" aria-label="Product thumbnail"></span></li>
    <li><span class="x">✕</span><span class="it"><b>Fontry Double Bed, Oak</b>2 X - $415.00</span><span class="th" role="img" aria-label="Product thumbnail"></span></li>
    <li><span class="x">✕</span><span class="it"><b>Fontry Double Bed, Oak</b>3 X - $615.00</span><span class="th" role="img" aria-label="Product thumbnail"></span></li>
  </ul>
  <div class="total"><span>TOTAL PRICE</span><span>$1245.00</span></div>
  <div class="btns"><span>VIEW CART</span><span>CHECKOUT</span></div>
</div>

<section class="abs hero">
  <div class="shot" role="img" aria-label="Photo of an open black laptop"></div>
  <div class="copy">
    <div class="l1">Lumavorp Year</div>
    <div class="l2">SALE</div>
    <div class="l3">Save up to</div>
    <div class="l4">50%<small>Voltaro</small></div>
    <div class="l5">on selected item</div>
  </div>
  <div class="abs arrow" style="left:0;top:120px"><svg width="8" height="10"><use href="#i-left"/></svg></div>
  <div class="abs arrow" style="right:0;top:120px"><svg width="8" height="10"><use href="#i-right"/></svg></div>
</section>
<div class="abs dots"><i></i><i></i><i></i><i></i></div>

<section class="abs featured">
  <div class="abs arrow" style="left:0;top:126px"><svg width="8" height="10"><use href="#i-left"/></svg></div>
  <div class="abs arrow" style="right:0;top:126px"><svg width="8" height="10"><use href="#i-right"/></svg></div>
  <div class="fcard" style="left:52px"><div class="pic t-black" role="img" aria-label="Photo of a black tablet"></div><div class="ribbon">HOT DEAL</div><div class="nm">Fontry Double Bed, Oak</div><div class="pr">$749</div><div class="old"><s>$849.50</s> <em>$13.50</em></div><div class="btn">View Product</div></div>
  <div class="fcard" style="left:243px"><div class="pic t-black" role="img" aria-label="Photo of a lens-style camera"></div><div class="ribbon">HOT DEAL</div><div class="nm">Fontry Double Bed, Oak</div><div class="pr">$749</div><div class="old"><s>$849.50</s> <em>$13.50</em></div><div class="btn">View Product</div></div>
  <div class="fcard" style="left:434px"><div class="pic t-wood" role="img" aria-label="Photo of wooden headphones"></div><div class="ribbon">HOT DEAL</div><div class="nm">Fontry Double Bed, Oak</div><div class="pr">$749</div><div class="old"><s>$849.50</s> <em>$13.50</em></div><div class="btn">View Product</div></div>
  <div class="fcard" style="left:625px"><div class="pic t-black" role="img" aria-label="Photo of a game console with controller"></div><div class="ribbon">HOT DEAL</div><div class="nm">Fontry Double Bed, Oak</div><div class="pr">$749</div><div class="old"><s>$849.50</s> <em>$13.50</em></div><div class="btn">View Product</div></div>
</section>

<aside class="abs box cats">
  <h3>Categories</h3>
  <ul><li>Sofas</li><li class="on">Gadgets</li><li>Lifestyle</li><li>Chairs</li><li>Tables</li><li>Beds</li><li>Storage</li><li>Lighting</li><li>Art</li><li>Homeware</li><li>Home Textiles</li><li>Designer</li><li>UNBOXED</li></ul>
</aside>

<aside class="abs box filters">
  <div class="grp"><h3>Thread Count</h3><ul><li>200</li><li>300</li></ul></div>
  <div class="grp"><h3>Bedding Size</h3><ul><li>Single</li><li>Double</li><li>Kingsize</li><li>Super King</li><li>Pillow Case</li></ul></div>
  <div class="grp"><h3>Availability</h3><ul><li>1 Week</li><li>1 Week</li><li>6 Week</li><li>10 Week</li></ul></div>
  <div class="grp"><h3>Colour</h3><ul><li>Blues</li><li>Browns</li><li>Colourful</li><li>Greys</li><li>Metallic</li><li>Neutrals</li><li>Oak</li><li>Patterned</li><li>Purples</li><li>Turquoise</li><li>Whites</li></ul></div>
  <div class="grp"><h3>Price</h3><ul><li>$0 - $ 250</li><li>$250 - $ 500</li><li>$500 - $ 750</li><li>$750 - $ 1000</li><li>$1000 - $ 1250</li></ul></div>
</aside>

<div class="abs sortbar">
  <span>Sort by price:</span><u>Low</u><span>|</span><span>High</span>
  <span style="margin-left:auto">Sort By</span><span class="sel">Position <span>▾</span></span>
  <span style="margin-left:10px">Show</span><span class="sel">Position <span>▾</span></span><span>Per Page</span>
</div>

<main class="abs grid">
  <div class="prod"><div class="pic t-black" role="img" aria-label="Photo of a DSLR camera"></div><div class="nm">Fontry Double Bed, Oak</div><div class="pr">$749</div><div class="foot"><span>Typical high street <s>$1,095*</s></span><i class="add"><svg width="14" height="14"><use href="#i-cart"/></svg></i></div></div>
  <div class="prod"><div class="pic t-silver" role="img" aria-label="Photo of over-ear headphones"></div><div class="nm">Fontry Double Bed, Oak</div><div class="pr">$749</div><div class="foot"><span>Typical high street <s>$1,095*</s></span><i class="add"><svg width="14" height="14"><use href="#i-cart"/></svg></i></div></div>
  <div class="prod"><div class="pic t-black" role="img" aria-label="Photo of sport sunglasses"></div><div class="nm">Fontry Double Bed, Oak</div><div class="pr">$749</div><div class="foot"><span>Typical high street <s>$1,095*</s></span><i class="add"><svg width="14" height="14"><use href="#i-cart"/></svg></i></div></div>

  <div class="prod"><div class="pic t-silver" role="img" aria-label="Photo of a record turntable"></div><div class="nm">Fontry Double Bed, Oak</div><div class="pr">$749</div><div class="foot"><span>Typical high street <s>$1,095*</s></span><i class="add"><svg width="14" height="14"><use href="#i-cart"/></svg></i></div></div>
  <div class="prod"><div class="pic t-black" role="img" aria-label="Photo of a wireless mouse"></div><div class="nm">Fontry Double Bed, Oak</div><div class="pr">$749</div><div class="foot"><span>Typical high street <s>$1,095*</s></span><i class="add"><svg width="14" height="14"><use href="#i-cart"/></svg></i></div></div>
  <div class="prod"><div class="pic t-white" role="img" aria-label="Photo of a filter water bottle"></div><div class="nm">Fontry Double Bed, Oak</div><div class="pr">$749</div><div class="foot"><span>Typical high street <s>$1,095*</s></span><i class="add"><svg width="14" height="14"><use href="#i-cart"/></svg></i></div></div>

  <div class="prod"><div class="pic t-white" role="img" aria-label="Photo of a round speaker"></div><div class="nm">Fontry Double Bed, Oak</div><div class="pr">$749</div><div class="foot"><span>Typical high street <s>$1,095*</s></span><i class="add"><svg width="14" height="14"><use href="#i-cart"/></svg></i></div></div>
  <div class="prod"><div class="pic t-black" role="img" aria-label="Photo of a black tablet"></div><div class="nm">Fontry Double Bed, Oak</div><div class="pr">$749</div><div class="foot"><span>Typical high street <s>$1,095*</s></span><i class="add"><svg width="14" height="14"><use href="#i-cart"/></svg></i></div></div>
  <div class="prod"><div class="pic t-black" role="img" aria-label="Photo of three smartphones"></div><div class="nm">Fontry Double Bed, Oak</div><div class="pr">$749</div><div class="foot"><span>Typical high street <s>$1,095*</s></span><i class="add"><svg width="14" height="14"><use href="#i-cart"/></svg></i></div></div>

  <div class="prod"><div class="pic t-black" role="img" aria-label="Photo of a lens-style camera"></div><div class="nm">Fontry Double Bed, Oak</div><div class="pr">$749</div><div class="foot"><span>Typical high street <s>$1,095*</s></span><i class="add"><svg width="14" height="14"><use href="#i-cart"/></svg></i></div></div>
  <div class="prod"><div class="pic t-wood" role="img" aria-label="Photo of a waffle maker"></div><div class="nm">Fontry Double Bed, Oak</div><div class="pr">$749</div><div class="foot"><span>Typical high street <s>$1,095*</s></span><i class="add"><svg width="14" height="14"><use href="#i-cart"/></svg></i></div></div>
  <div class="prod"><div class="pic t-black" role="img" aria-label="Photo of a sports watch"></div><div class="nm">Fontry Double Bed, Oak</div><div class="pr">$749</div><div class="foot"><span>Typical high street <s>$1,095*</s></span><i class="add"><svg width="14" height="14"><use href="#i-cart"/></svg></i></div></div>

  <div class="prod"><div class="pic t-silver" role="img" aria-label="Photo of a steel smartwatch"></div><div class="nm">Fontry Double Bed, Oak</div><div class="pr">$749</div><div class="foot"><span>Typical high street <s>$1,095*</s></span><i class="add"><svg width="14" height="14"><use href="#i-cart"/></svg></i></div></div>
  <div class="prod"><div class="pic t-thermo" role="img" aria-label="Photo of a round thermostat on a wooden wall"></div><div class="nm">Fontry Double Bed, Oak</div><div class="pr">$749</div><div class="foot"><span>Typical high street <s>$1,095*</s></span><i class="add"><svg width="14" height="14"><use href="#i-cart"/></svg></i></div></div>
  <div class="prod"><div class="pic t-black" role="img" aria-label="Photo of a solid state drive"></div><div class="nm">Fontry Double Bed, Oak</div><div class="pr">$749</div><div class="foot"><span>Typical high street <s>$1,095*</s></span><i class="add"><svg width="14" height="14"><use href="#i-cart"/></svg></i></div></div>

  <div class="prod"><div class="pic t-silver" role="img" aria-label="Photo of a white smartphone"></div><div class="nm">Fontry Double Bed, Oak</div><div class="pr">$749</div><div class="foot"><span>Typical high street <s>$1,095*</s></span><i class="add"><svg width="14" height="14"><use href="#i-cart"/></svg></i></div></div>
  <div class="prod"><div class="pic t-wood" role="img" aria-label="Photo of wooden headphones"></div><div class="nm">Fontry Double Bed, Oak</div><div class="pr">$749</div><div class="foot"><span>Typical high street <s>$1,095*</s></span><i class="add"><svg width="14" height="14"><use href="#i-cart"/></svg></i></div></div>
  <div class="prod"><div class="pic t-black" role="img" aria-label="Photo of a game controller"></div><div class="nm">Fontry Double Bed, Oak</div><div class="pr">$749</div><div class="foot"><span>Typical high street <s>$1,095*</s></span><i class="add"><svg width="14" height="14"><use href="#i-cart"/></svg></i></div></div>

  <div class="prod"><div class="pic t-black" role="img" aria-label="Photo of a game console with controller"></div><div class="nm">Fontry Double Bed, Oak</div><div class="pr">$749</div><div class="foot"><span>Typical high street <s>$1,095*</s></span><i class="add"><svg width="14" height="14"><use href="#i-cart"/></svg></i></div></div>
  <div class="prod"><div class="pic t-tv" role="img" aria-label="Photo of a flat screen television"></div><div class="nm">Fontry Double Bed, Oak</div><div class="pr">$749</div><div class="foot"><span>Typical high street <s>$1,095*</s></span><i class="add"><svg width="14" height="14"><use href="#i-cart"/></svg></i></div></div>
  <div class="prod"><div class="pic t-silver" role="img" aria-label="Photo of a compact desktop computer"></div><div class="nm">Fontry Double Bed, Oak</div><div class="pr">$749</div><div class="foot"><span>Typical high street <s>$1,095*</s></span><i class="add"><svg width="14" height="14"><use href="#i-cart"/></svg></i></div></div>
</main>

<nav class="abs pager">
  <svg width="14" height="10" viewBox="0 0 14 10"><path d="M13 5H2M5 1L1 5l4 4" fill="none" stroke="#333" stroke-width="1.5"/></svg>
  <div class="pg"><span class="on">1</span><span>2</span><span>3</span><span>4</span><span>5</span></div>
  <div class="pg end"><span>...</span></div>
  <div class="pg end"><span>100</span></div>
  <svg width="14" height="10" viewBox="0 0 14 10"><path d="M1 5h11M9 1l4 4-4 4" fill="none" stroke="#333" stroke-width="1.5"/></svg>
</nav>
<div class="abs status">Displaying 1 to 12 (of 100 products)</div>

<footer class="abs footer">
  <div class="fcol" style="left:183px"><h5>Contact Us</h5><ul>
    <li><svg width="10" height="12" viewBox="0 0 24 30"><path d="M12 0a10 10 0 0 0-10 10c0 8 10 20 10 20s10-12 10-20A10 10 0 0 0 12 0zm0 14a4 4 0 1 1 0-8 4 4 0 0 1 0 8z" fill="#fff"/></svg>12 Fernwick Row, Dalbury</li>
    <li><svg width="11" height="11" fill="#fff"><use href="#i-phone"/></svg>+000 (000) 0000</li>
    <li><svg width="12" height="9" viewBox="0 0 24 18"><rect width="24" height="18" fill="#fff"/><path d="M0 0l12 9 12-9" fill="none" stroke="#3b3c3e" stroke-width="2"/></svg>mail@example.com</li>
  </ul></div>
  <div class="fcol" style="left:399px"><h5>Information</h5><ul><li>About Us</li><li>Privacy Policy</li><li>Terms &amp; Conditions</li><li>Secure Payment</li></ul></div>
  <div class="fcol" style="left:614px"><h5>Costumer Service</h5><ul><li>Contact Us</li><li>Return</li><li>FAQ</li><li>Site Map</li></ul></div>
  <div class="fcol" style="left:830px"><h5>My Account</h5><ul><li>My Account</li><li>Order History</li><li>Wish List</li><li>Newsletter</li></ul></div>
</footer>

<div class="abs bottom">
  <div class="copy">© 2014 Lumavorp. All rights reserved.</div>
  <div class="social"><span>plaztrove</span><span>chirpwell</span><span>plusvane</span></div>
</div>

</body>
</html>
```